Lotus Market Hall VIP Card(Magnetic strip plastic card)

We need Fancy,Simple,VIP customer card design for a grocery store name"Lotus Market Hall", Chinese name"福润商场“.Major color should be Dark red. This design is based on a VIP gift card project, which means design should consider about the back side with magnetic strip area and mostly it will be plastic material.

Target Market(s)

Rich Customers

Industry/Entity Type

Grocery Store

Contact Information for Business Card

People actually put more than $1000 into the card for shopping

Font styles to use
Serif
Sans Serif
Decorative
Script
Other font styles liked:
• Fancy

Colors
ec1f27
fbed22

Requirements
Must have
• Red color
Nice to have
• Better logo transformation.

```html
<!DOCTYPE html>
<html lang="en">
<head>
<meta charset="utf-8">
<title>Lotus Market Hall – VIP Card</title>
<link href="https://fonts.googleapis.com/css2?family=Alegreya:wght@400&family=Noto+Serif+SC:wght@400&display=swap" rel="stylesheet">
<style>
  :root {
    --page-bg: #ecebe8;
    --card-bg: #ffffff;
    --brand-red: #b3141c;
    --ink: #1e1e1e;
    --strip: #1c1a1a;
    --card-shadow: rgba(0, 0, 0, 0.18);
  }
  * { margin: 0; padding: 0; box-sizing: border-box; }
  html, body {
    width: 1200px;
    height: 900px;
    overflow: hidden;
    background: var(--page-bg);
  }
  body {
    font-family: "Alegreya", "Noto Serif SC", serif;
    color: var(--ink);
  }
  .card-sheet {
    width: 1200px;
    height: 900px;
    display: flex;
    align-items: center;
    justify-content: center;
    gap: 40px;
  }
  .card {
    position: relative;
    width: 540px;
    height: 341px;
    background: var(--card-bg);
    border-radius: 18px;
    overflow: hidden;
    box-shadow: 0 6px 18px var(--card-shadow);
  }

  .brand-name {
    color: var(--brand-red);
    font-weight: 400;
    text-align: center;
    line-height: 1.05;
  }
  .brand-name .name-zh {
    display: block;
    font-family: "Noto Serif SC", "Alegreya", serif;
    letter-spacing: 0.08em;
  }
  .brand-name .name-en { display: block; }

  /* Front */
  .card-front {
    display: flex;
    align-items: center;
    justify-content: center;
  }
  .card-front .brand-name .name-zh { font-size: 46px; }
  .card-front .brand-name .name-en { font-size: 20px; margin-top: 8px; }
  .vip-tag {
    position: absolute;
    right: 30px;
    bottom: 24px;
    color: var(--brand-red);
    font-size: 20px;
    letter-spacing: 0.3em;
  }

  /* Back */
  .magnetic-strip {
    position: absolute;
    left: 0;
    top: 24px;
    width: 100%;
    height: 48px;
    background: var(--strip);
  }
  .card-back .brand-name {
    position: absolute;
    top: 92px;
    right: 30px;
  }
  .card-back .brand-name .name-zh { font-size: 30px; }
  .card-back .brand-name .name-en { font-size: 13px; margin-top: 5px; }

  .contact-person {
    position: absolute;
    left: 34px;
    top: 160px;
  }
  .person-name {
    color: var(--brand-red);
    font-size: 25px;
    line-height: 1.1;
  }
  .person-role {
    font-size: 15px;
    margin-left: 10px;
  }
  .contact-details {
    position: absolute;
    left: 44px;
    bottom: 22px;
    font-size: 13.5px;
    line-height: 1.55;
  }
  .contact-details .label,
  .contact-details .web { color: var(--brand-red); }
  .contact-details .sep { margin-left: 8px; }
</style>
</head>
<body>
<main class="card-sheet">

  <section class="card card-front" aria-label="VIP card front">
    <div class="brand-name">
      <span class="name-zh">福润商场</span>
      <span class="name-en">Lotus Market Hall</span>
    </div>
    <span class="vip-tag">VIP</span>
  </section>

  <section class="card card-back" aria-label="VIP card back">
    <div class="magnetic-strip" aria-hidden="true"></div>

    <div class="brand-name">
      <span class="name-zh">福润商场</span>
      <span class="name-en">Lotus Market Hall</span>
    </div>

    <div class="contact-person">
      <p class="person-name">Daniel Hart</p>
      <p class="person-role">Managing Director</p>
    </div>

    <div class="contact-details">
      <p>18 Orchard Lane, Riverton, 40821</p>
      <p><span class="label">T:</span> (052) 418 207 635<span class="sep label">F:</span> (052) 418207636<span class="sep label">M:</span> (052)771093248</p>
      <p><span class="label">E:</span> hello@lotusmarkethall.com<span class="sep web">www.lotusmarkethall.com</span></p>
    </div>
  </section>

</main>
</body>
</html>
```